Flyer-Design für Schädlingsbekämpfung
Sehr gute Kommunikation! Produkt sehr gut!! Gerne wieder
Zielgruppe
Schädlingsbekämpfung- und Prophylaxe, Service Monitoring, Gastronomie und Industrie, alle Lebendsmittel verarbeitenden Betriebe
Aufgabenstellung
Schwerpunkt soll das HACCP Konzept sein, welches bei allen Lebensmittelverarbeiteten Betrieben gesetzlich vorgeschrieben ist,

```html
<!DOCTYPE html>
<html lang="de">
<head>
<meta charset="utf-8">
<title>Schädlingsfrei Jonas Walberg – Flyer</title>
<link href="https://fonts.googleapis.com/css2?family=Poppins:wght@400;500;600;700;800&display=swap" rel="stylesheet">
<style>
  :root{
    --green:#138a3c;
    --green-dark:#0f7431;
    --ink:#1c1c1c;
    --white:#ffffff;
    --stage:#e6e6e6;
    --deco:#efefef;
  }
  *{box-sizing:border-box;margin:0;padding:0}
  html,body{width:1200px;height:817px;overflow:hidden;background:var(--stage);font-family:'Poppins',sans-serif}
  .flyer{position:absolute;top:101px;width:436px;height:618px;background:var(--white);overflow:hidden}
  .flyer--front{left:132px}
  .flyer--back{left:624px}
  .deco-fill{position:absolute;background:var(--deco)}
  .brand{position:absolute;display:flex;align-items:center;gap:8px;z-index:2}
  .brand__name{color:var(--green);font-weight:600;font-size:15px;line-height:1.15;text-align:right}
  .brand__name small{display:block;font-size:10px}
  .brand__mark{width:62px;height:62px;border-radius:50%;background:var(--green)}
  .photo{position:absolute}
  .title-band{position:absolute;left:0;top:98px;width:436px;height:75px;background:var(--green);color:var(--white);font-weight:800;font-size:23px;line-height:1.08;padding:17px 0 0 39px;letter-spacing:.2px}
  .corner{position:absolute;width:0;height:0;border-style:solid}
  .service-panel{position:absolute;left:246px;top:196px;width:190px;height:188px;background:var(--green);color:var(--white);padding:28px 0 0 12px}
  .service-panel h3{font-size:11.5px;font-weight:800;line-height:1.25;margin-bottom:6px}
  .service-panel li{list-style:none;font-size:9.6px;line-height:16px;display:flex;align-items:center;gap:6px}
  .tick{width:9px;height:8px;flex:none}
  .phone{position:absolute;left:0;top:467px;width:370px;height:43px;background:var(--ink);border-radius:0 8px 8px 0;color:var(--white);font-weight:700;font-size:32px;display:flex;align-items:center;padding-left:30px;gap:10px}
  .phone__icon{width:32px;height:32px;border-radius:50%;background:var(--white);display:flex;align-items:center;justify-content:center}
  .haccp-row{position:absolute;left:30px;top:521px;display:flex;gap:12px;align-items:flex-end}
  .haccp-step{width:44px;text-align:center;font-size:7.5px;color:var(--ink)}
  .haccp-step svg{display:block;margin:0 auto 2px;width:30px;height:28px}
  .haccp-badge{position:absolute;left:373px;top:525px;width:54px;height:38px;background:var(--green);color:var(--white);font-size:9px;font-weight:700;text-align:center;line-height:1.2;padding-top:7px}
  .haccp-badge::before{content:"";position:absolute;left:-12px;top:0;border-style:solid;border-width:19px 12px 19px 0;border-color:transparent var(--green-dark) transparent transparent}
  .footer{position:absolute;left:0;bottom:0;width:436px;background:var(--green);color:var(--white);font-weight:600}
  .footer--front{height:44px;display:flex;align-items:center;gap:22px;padding-left:32px;font-size:14px}
  .contact{display:flex;align-items:center;gap:7px}
  .contact svg{width:20px;height:18px}
  .benefit-band{position:absolute;left:0;top:116px;width:313px;height:118px;background:var(--green);color:var(--white);padding:12px 0 0 30px}
  .benefit{display:flex;align-items:center;font-size:12px;font-weight:700;line-height:1.12;margin-bottom:7px}
  .benefit svg{width:16px;height:14px;margin-right:8px;flex:none}
  .benefit span{border-left:1.5px solid var(--white);padding-left:5px;min-height:24px;display:flex;align-items:center}
  .footer--back{height:83px;font-size:11.5px;line-height:1.45}
  .address{position:absolute;left:42px;top:14px;display:flex;gap:10px;align-items:flex-start}
  .address div{border-left:1.5px solid var(--white);padding-left:6px}
  .digital{position:absolute;left:244px;top:14px;display:flex;flex-direction:column;gap:12px}
  .digital .contact{gap:10px}
  .digital .contact span{border-left:1.5px solid var(--white);padding-left:6px}
</style>
</head>
<body>

<section class="flyer flyer--front">
  <div class="deco-fill" role="img" aria-label="Dekorative Schraffur" style="left:0;top:0;width:140px;height:98px"></div>
  <div class="brand" style="left:178px;top:18px">
    <div class="brand__name">Schädlingsfrei<br>Jonas Walberg<small>Bad Kreuznach</small></div>
    <div class="brand__mark"></div>
  </div>

  <div class="title-band">SCHÄDLINGSBEKÄMPFUNG,<br>HOLZ- UND BAUTENSCHUTZ</div>
  <div class="corner" style="left:0;top:98px;border-width:38px 38px 0 0;border-color:var(--ink) transparent transparent transparent"></div>

  <div class="photo" role="img" aria-label="Foto: Schädlingsbekämpfer im Schutzanzug sprüht in einer hellen Küche" style="left:0;top:173px;width:436px;height:343px;background:linear-gradient(90deg,#d9dbe0 0%,#eeeae4 45%,#c8a57c 100%)"></div>

  <div class="service-panel">
    <h3>IHR FACHBETRIEB<br>IN BAD KREUZNACH FÜR:</h3>
    <ul>
      <li><svg class="tick" viewBox="0 0 10 8"><path d="M1 4l3 3 5-6" fill="none" stroke="#fff" stroke-width="1.5"/></svg>Holz- und Bautenschutz</li>
      <li><svg class="tick" viewBox="0 0 10 8"><path d="M1 4l3 3 5-6" fill="none" stroke="#fff" stroke-width="1.5"/></svg>Hausbockbekämpfung</li>
      <li><svg class="tick" viewBox="0 0 10 8"><path d="M1 4l3 3 5-6" fill="none" stroke="#fff" stroke-width="1.5"/></svg>Hausschwammbekämpfung</li>
      <li><svg class="tick" viewBox="0 0 10 8"><path d="M1 4l3 3 5-6" fill="none" stroke="#fff" stroke-width="1.5"/></svg>Pilz/ Schimmelpilzsanierung</li>
      <li><svg class="tick" viewBox="0 0 10 8"><path d="M1 4l3 3 5-6" fill="none" stroke="#fff" stroke-width="1.5"/></svg>Schädlingsbekämpfung</li>
      <li><svg class="tick" viewBox="0 0 10 8"><path d="M1 4l3 3 5-6" fill="none" stroke="#fff" stroke-width="1.5"/></svg>Taubenabwehr</li>
      <li><svg class="tick" viewBox="0 0 10 8"><path d="M1 4l3 3 5-6" fill="none" stroke="#fff" stroke-width="1.5"/></svg>HACCP Service</li>
    </ul>
  </div>

  <div class="phone">
    <span class="phone__icon"><svg width="18" height="18" viewBox="0 0 24 24"><path d="M6.6 10.8a15 15 0 006.6 6.6l2.2-2.2c.3-.3.7-.4 1-.2 1.1.4 2.3.6 3.6.6.6 0 1 .4 1 1V20c0 .6-.4 1-1 1A17 17 0 013 4c0-.6.4-1 1-1h3.5c.6 0 1 .4 1 1 0 1.3.2 2.5.6 3.6.1.3 0 .7-.2 1z" fill="#1c1c1c"/></svg></span>
    0671 / 555 01 234
  </div>

  <div class="haccp-row">
    <div class="haccp-step"><svg viewBox="0 0 30 28"><path d="M15 2L28 26H2z" fill="none" stroke="#138a3c" stroke-width="2"/><circle cx="15" cy="18" r="3.5" fill="none" stroke="#1c1c1c" stroke-width="1.5"/></svg>HAZARD</div>
    <div class="haccp-step"><svg viewBox="0 0 30 28"><circle cx="11" cy="11" r="7" fill="none" stroke="#138a3c" stroke-width="2"/><path d="M16 16l8 9" stroke="#1c1c1c" stroke-width="2.5"/></svg>ANALYSIS</div>
    <div class="haccp-step"><svg viewBox="0 0 30 28"><path d="M15 2L28 26H2z" fill="none" stroke="#138a3c" stroke-width="2"/><path d="M15 10v8M15 21v2" stroke="#1c1c1c" stroke-width="2.2"/></svg>CRITICAL</div>
    <div class="haccp-step"><svg viewBox="0 0 30 28"><rect x="6" y="22" width="16" height="4" fill="#1c1c1c"/><path d="M12 4h5v14h-5z" fill="#1c1c1c"/><circle cx="23" cy="21" r="5" fill="#138a3c"/><path d="M20.5 21l2 2 3-4" fill="none" stroke="#fff" stroke-width="1.4"/></svg>CONTROL</div>
    <div class="haccp-step"><svg viewBox="0 0 30 28"><circle cx="10" cy="17" r="8" fill="none" stroke="#1c1c1c" stroke-width="2"/><path d="M6 16l4 4 9-14" fill="none" stroke="#138a3c" stroke-width="2.5"/><circle cx="24" cy="6" r="2.5" fill="#1c1c1c"/><path d="M22 10h4v16h-4z" fill="#1c1c1c"/></svg>POINTS</div>
  </div>
  <div class="haccp-badge">HACCP<br>Konzept</div>

  <footer class="footer footer--front">
    <span class="contact"><svg viewBox="0 0 20 20"><circle cx="10" cy="10" r="8" fill="none" stroke="#fff" stroke-width="1.6"/><path d="M2 10h16M10 2c-3 3-3 13 0 16M10 2c3 3 3 13 0 16" fill="none" stroke="#fff" stroke-width="1.2"/></svg>www.walberg-kh.de</span>
    <span class="contact"><svg viewBox="0 0 22 16"><rect x="1" y="1" width="20" height="14" fill="none" stroke="#fff" stroke-width="1.6"/><path d="M1 1l10 8 10-8" fill="none" stroke="#fff" stroke-width="1.6"/></svg>walberg@walberg-kh.de</span>
  </footer>
</section>

<section class="flyer flyer--back">
  <div class="deco-fill" role="img" aria-label="Dekorative Schraffur" style="left:280px;top:0;width:156px;height:100px;clip-path:polygon(100% 0,100% 100%,0 100%)"></div>
  <div class="photo" role="img" aria-label="Foto: Schädlingsbekämpfer im Schutzanzug mit Sprühlanze, Schaben auf dem Boden" style="left:71px;top:70px;width:365px;height:243px;background:linear-gradient(160deg,#efeeec 0%,#d9d2c8 55%,#a88f7a 100%)"></div>
  <div class="brand" style="left:28px;top:30px">
    <div class="brand__name">Schädlingsfrei<br>Jonas Walberg<small>Bad Kreuznach</small></div>
    <div class="brand__mark"></div>
  </div>

  <div class="benefit-band">
    <div class="benefit"><svg viewBox="0 0 16 14"><path d="M1 7l5 5 9-11" fill="none" stroke="#fff" stroke-width="1.8"/></svg><span>DAUERHAFTE<br>ENTFERNUNG / UMSIEDLUNG</span></div>
    <div class="benefit"><svg viewBox="0 0 16 14"><path d="M1 7l5 5 9-11" fill="none" stroke="#fff" stroke-width="1.8"/></svg><span>DCHNELL, NACHHALTIG UND EINFACH</span></div>
    <div class="benefit"><svg viewBox="0 0 16 14"><path d="M1 7l5 5 9-11" fill="none" stroke="#fff" stroke-width="1.8"/></svg><span>FACHGERECHTE BEKÄMPFUNG<br>MIT ERFAHRUNG</span></div>
  </div>

  <div class="deco-fill" role="img" aria-label="Dekorative Schraffur" style="left:0;top:234px;width:71px;height:301px"></div>

  <div class="photo" role="img" aria-label="Foto: Schädlingsbekämpfung in einer Lagerhalle" style="left:71px;top:319px;width:194px;height:98px;background:linear-gradient(135deg,#b7c0c8,#e4e8ea)"></div>
  <div class="photo" role="img" aria-label="Foto: Sprühlanze über grünen Pflanzen" style="left:271px;top:319px;width:165px;height:98px;background:linear-gradient(135deg,#4f8f2e,#7fbf45)"></div>
  <div class="photo" role="img" aria-label="Foto: Drucksprüher an einem Baum" style="left:71px;top:422px;width:194px;height:98px;background:linear-gradient(135deg,#6d8a3c,#a7c06a)"></div>
  <div class="photo" role="img" aria-label="Foto: Person im Schutzanzug vor dunkler Wand" style="left:271px;top:422px;width:165px;height:98px;background:linear-gradient(135deg,#1f2329,#4a4f57)"></div>

  <footer class="footer footer--back">
    <div class="corner" style="left:0;top:0;border-width:48px 48px 0 0;border-color:var(--ink) transparent transparent transparent"></div>
    <div class="address">
      <svg width="20" height="26" viewBox="0 0 20 26" style="margin-top:12px"><path d="M10 1a8 8 0 00-8 8c0 6 8 16 8 16s8-10 8-16a8 8 0 00-8-8z" fill="#fff"/><circle cx="10" cy="9" r="3" fill="#138a3c"/></svg>
      <div>SJW Bad Kreuznach<br>Lindenweg 12-14<br>55545 Bad Kreuznach</div>
    </div>
    <div class="digital">
      <span class="contact"><svg viewBox="0 0 22 16"><rect x="1" y="1" width="20" height="14" fill="none" stroke="#fff" stroke-width="1.6"/><path d="M1 1l10 8 10-8" fill="none" stroke="#fff" stroke-width="1.6"/></svg><span>walberg@walberg-kh.de</span></span>
      <span class="contact"><svg viewBox="0 0 20 20"><circle cx="10" cy="10" r="8" fill="none" stroke="#fff" stroke-width="1.6"/><path d="M2 10h16M10 2c-3 3-3 13 0 16M10 2c3 3 3 13 0 16" fill="none" stroke="#fff" stroke-width="1.2"/></svg><span>www.walberg-kh.de</span></span>
    </div>
  </footer>
</section>

</body>
</html>
```